Copper lark buildworks

Copper lark buildworks is a small construction company.
Who is a licenced builder, Carpenter, joiner,
working on heritage ,new build, speacial projects and sometimes furniture

Industry/Entity Type

Construction

```html
<!DOCTYPE html>
<html lang="en">
<head>
<meta charset="utf-8">
<title>Copper lark buildworks – Business Card</title>
<link rel="stylesheet" href="https://fonts.googleapis.com/css2?family=Open+Sans:wght@400;600;700&display=swap">
<style>
  :root {
    --backdrop: #e9e9e9;
    --card: #ffffff;
    --ink: #231f20;
    --brand-green: #02923e;
    --on-green: #ffffff;
  }
  * { box-sizing: border-box; margin: 0; padding: 0; }
  html, body {
    width: 1200px;
    height: 1000px;
    overflow: hidden;
    background: var(--backdrop);
    font-family: "Open Sans", Arial, sans-serif;
  }
  .business-card {
    position: absolute;
    left: 100px;
    top: 190px;
    width: 1000px;
    height: 621px;
    background: var(--card);
  }
  .holder-name {
    position: absolute;
    top: 64px;
    left: 0;
    width: 100%;
    text-align: center;
    font-size: 35px;
    font-weight: 400;
    color: var(--ink);
  }
  .roof-band {
    position: absolute;
    left: 0;
    top: 0;
    width: 1000px;
    height: 621px;
  }
  .roof-band polygon { fill: var(--brand-green); }
  .brand-name {
    position: absolute;
    top: 346px;
    left: 19px;
    width: 963px;
    text-align: center;
    font-size: 64px;
    font-weight: 700;
    line-height: 1.2;
    color: var(--on-green);
  }
  .phone-number {
    position: absolute;
    top: 527px;
    left: 270px;
    font-size: 38px;
    font-weight: 700;
    color: var(--ink);
    letter-spacing: 25px;
  }
</style>
</head>
<body>
  <main class="business-card">
    <p class="holder-name">Morgan Hale</p>
    <svg class="roof-band" viewBox="0 0 1000 621" aria-hidden="true">
      <polygon points="19,492 19,268 487,167 982,268 982,492"/>
    </svg>
    <p class="brand-name">Copper lark buildworks</p>
    <p class="phone-number">0417362954</p>
  </main>
</body>
</html>
```